Family business needs stationery redesign with new logo

Family owned company, established in 1987 wanting a brand 'refresh'. We are an electrical, refrigeration and construction company based in the Barkly Region Northern Territory, Australia. We have a new logo we would like to use which is uploaded along with our current letterhead and email signature. We are also dropping the word 'contractors' so please do not include this on any designs. Please note also, the 'orange' color used in our logo and designs should be Northern Territory red ochre which is as follows:

RGB (Hex): #C75B12
PantoneĀ® 159 C
CMYK: 1 / 74 / 100 / 7

We are needing our stationery redesigned using our new logo. Please include letterheads, business cards, envelopes, and email signatures.

We currently use our business letterheads for quotations, invoices, letters, HR matters, and internal memos.

We also need a separate simplified letterhead for internal paperwork such as employee leave forms, meeting agendas, and meeting minutes etc.

Reason: Needing more submissions of full package designs. We are wanting all our stationery, including business cards, letterheads, email signatures, envelopes, etc to be cohesive. We also require ALL the information, as supplied on our template letterhead, to be included on the new letterhead designs. including electrical license no.etc Thank you, R&W

Reason: needing more time as work has got in the way of looking over designs. A lot of designs not meeting the brief/criteria.

Industry/Entity Type

Business

Colors
0355a3
f37122

Requirements
Must have
• The 'orange' color used in the designs should be Northern Territory red ochre which is as follows:
• RGB (Hex): #C75B12
• PantoneĀ® 159 C
• CMYK: 1 / 74 / 100 / 7
• ***MUST INCLUDE ALL INFORMATION THAT IS ON OUR CURRENT LETTERHEAD***
Should not have
• Please do not include the word 'contractors'

```html
<!DOCTYPE html>
<html lang="en">
<head>
<meta charset="utf-8">
<title>R&amp;W Stationery</title>
<link rel="stylesheet" href="https://fonts.googleapis.com/css2?family=Arimo:wght@400;700&family=Open+Sans:wght@400;600&display=swap">
<style>
  :root{
    --navy:#1b2f6b;
    --ochre:#c75b12;
    --paper:#ffffff;
    --backdrop:#e4e4e4;
    --ink:#333a45;
    --rule:#d8d8d8;
  }
  *{box-sizing:border-box;margin:0;padding:0}
  html,body{width:1200px;height:715px;overflow:hidden;background:var(--backdrop)}
  .board{position:relative;width:1200px;height:715px;font-family:"Arimo",Arial,sans-serif}
  .piece{position:absolute;background:var(--paper);overflow:hidden;box-shadow:0 1px 3px rgba(0,0,0,.18)}
  .swoosh{position:absolute;left:0;bottom:0;display:block}
  .wordmark{position:absolute;font-family:"Arimo",Arial,sans-serif;font-weight:700;color:var(--navy);transform:translate(-50%,-50%);white-space:nowrap;line-height:1}
  .wordmark.on-dark{color:#fff}

  /* Letterhead */
  .letterhead{left:188px;top:66px;width:440px;height:620px;font-family:"Open Sans",Arial,sans-serif}
  .letterhead .wordmark{left:222px;top:64px;font-size:40px}
  .letterhead .tagline{position:absolute;left:0;right:0;top:98px;text-align:center;font-size:9.6px;color:var(--navy)}
  .letterhead .tagline .dash{color:var(--ochre)}
  .letterhead .body{position:absolute;left:33px;top:225px;width:383px;font-size:7.2px;line-height:9.6px;color:var(--ink)}
  .letterhead .body p{margin-bottom:9.6px}
  .letterhead .signoff{position:absolute;left:33px;top:405px;font-size:7.4px;color:#222}
  .letterhead .footer{position:absolute;left:0;right:0;bottom:8px;text-align:center;color:#fff;font-size:7.4px;line-height:10.8px}
  .letterhead .footer b{color:var(--ochre);font-weight:600}

  /* Business cards */
  .card{width:240px;height:137px;border-radius:6px}
  .card-front{left:48px;top:160px}
  .card-front .wordmark{left:60px;top:68px;font-size:30px}
  .card-front .divider{position:absolute;left:118px;top:24px;width:1px;height:78px;background:var(--rule)}
  .card-back{background:var(--navy)}
  .card-back .wordmark{left:120px;top:66px;font-size:44px}
  .card-back .est{position:absolute;left:0;right:0;top:112px;text-align:center;font-family:"Open Sans",Arial,sans-serif;font-size:9.6px;letter-spacing:.5px;color:#fff}
  .card-back.alt .est{color:var(--ochre)}
  .card-back-a{left:48px;top:324px}
  .card-back-b{left:48px;top:482px}

  .contact .name{font-weight:700;color:var(--navy);text-transform:uppercase}
  .contact .role{color:var(--ochre)}
  .contact .addr,.contact li{color:#444}
  .contact ul{list-style:none}
  .contact li{display:flex;align-items:center}
  .contact li svg{flex:none}
  .card-front .contact{position:absolute;left:134px;top:31px}
  .card-front .name{font-size:8.8px}
  .card-front .role{font-size:6.8px;margin-bottom:5px}
  .card-front .addr{font-size:6px;line-height:7.6px;margin-bottom:5px}
  .card-front li{font-size:6px;line-height:9px}
  .card-front li svg{width:6px;height:6px;margin-right:3px}

  .card-wide{left:748px;top:44px;width:284px;height:138px;border-radius:0}
  .card-wide .wordmark{left:75px;top:67px;font-size:38px}
  .card-wide .divider{position:absolute;left:146px;top:14px;width:1px;height:102px;background:var(--rule)}
  .card-wide .contact{position:absolute;left:167px;top:16px}
  .card-wide .name{font-size:11.6px}
  .card-wide .role{font-size:8.8px;margin-bottom:6px}
  .card-wide .addr{font-size:7.6px;line-height:10.4px;margin-bottom:4px}
  .card-wide li{font-size:7.6px;line-height:11.4px}
  .card-wide li svg{width:7px;height:7px;margin-right:4px}

  /* Envelopes */
  .envelope{width:518px;border-radius:0}
  .envelope-back{left:642px;top:210px;height:232px}
  .envelope-back .flap{position:absolute;left:0;top:0;display:block}
  .envelope-back .wordmark{left:259px;top:44px;font-size:30px}
  .envelope-front{left:642px;top:456px;height:232px}
  .envelope-front .wordmark{left:76px;top:47px;font-size:38px}
  .envelope-front .return{position:absolute;left:25px;top:82px;font-family:"Open Sans",Arial,sans-serif;font-size:8px;line-height:11px;color:#444}
</style>
</head>
<body>
<main class="board">

  <!-- Letterhead -->
  <section class="piece letterhead" aria-label="Letterhead">
    <div class="wordmark">R&amp;W</div>
    <p class="tagline">Electrical <span class="dash">-</span> Refrigeration <span class="dash">-</span> Building Services</p>
    <div class="body">
      <p>Lorem ipsum dolor sit amet, consectetur adipiscing elit. Donec orci purus, luctus vitae dignissim eu, iaculis sed purus. Vivamus faucibus, ipsum nec aliquet viverra, leo mauris condimentum ligula, sit amet sagittis enim ligula quis arcu. Nam egestas tortor id nisi porttitor mattis. In tortor ante, ultricies in suscipit a, tempus non massa. Vivamus et auctor mi.</p>
      <p>Nulla facilisi. Nunc at ligula a. Phasellus nec eros mauris, et scelerisque orci. Donec malesuada orci vitae nulla accumsan pellentesque. Quisque accumsan iaculis magna sit amet fringilla. Maecenas consequat, magna eget tincidunt rutrum, dui arcu rutrum mi, id feugiat ante nisi eu risus. Vestibulum nunc orci, rhoncus a placerat in, ultricies eu nunc. Aenean varius eros, vel fringilla nisi suscipit eget.</p>
      <p>Mauris pretium luctus est, eu sagittis nulla at porttitor. Mauris a justo et tellus interdum tristique. Sed id augue vitae urna tempus vulputate vel aliquet a quam. Pellentesque arcu velit, cursus et malesuada ut, consequat et diam. Nullam ullamcorper, nisi ac ullamcorper vitae, rhoncus et arcu. In ultricies ultricies nulla, ut rutrum nisi iaculis at. Donec ornare faucibus ornare faucibus.</p>
      <p>Curabitur sit amet lectus ultricies. Morbi semper, est id tincidunt gravida, sem arcu adipiscing lacus, ac bibendum dui lorem vel nunc. Quisque nec diam sed risus consectetur a ccumsan quis quis nibh. Vestibulum id purus lorem.</p>
    </div>
    <p class="signoff">Mark Ellis</p>
    <svg class="swoosh" width="440" height="90" viewBox="0 0 440 90" aria-hidden="true">
      <path d="M0,0 Q230,36 440,34 L440,37 Q230,40 0,4 Z" fill="var(--ochre)"/>
      <path d="M0,6 Q230,42 440,39 L440,90 L0,90 Z" fill="var(--navy)"/>
    </svg>
    <div class="footer">
      <div>62 Ridley St, PO Box, Barkly Creek NT. 0862</div>
      <div>ABN 40 219 773 | Refrigerant Trading Authorisation 604218 | NT Electrical Contractors License 61432</div>
      <div><b>P</b> : 08 8941 2036 &nbsp;<b>F</b> : 08 8941 2037 &nbsp;<b>E</b> : info@rwservices.com.au &nbsp;<b>W</b> : rwservices.com.au</div>
    </div>
  </section>

  <!-- Business card, front -->
  <section class="piece card card-front" aria-label="Business card front">
    <div class="wordmark">R&amp;W</div>
    <div class="divider"></div>
    <div class="contact">
      <p class="name">Lena Marsh</p>
      <p class="role">CEO/Founder</p>
      <p class="addr">4210 Wattle Grove Lane<br>Alice Springs, NT 0871</p>
      <ul>
        <li><svg viewBox="0 0 10 10"><path d="M2 0.5 L4 2.8 L3 4 Q4.5 6 6 7 L7.2 6 L9.5 8 L8 9.6 Q4 9 0.4 2 Z" fill="var(--navy)"/></svg>612 408 3317</li>
        <li><svg viewBox="0 0 10 10"><rect x="2.5" y="0.5" width="5" height="3" fill="var(--navy)"/><rect x="0.5" y="4" width="9" height="5.5" rx="1" fill="var(--navy)"/></svg>455 873 1206</li>
        <li><svg viewBox="0 0 10 10"><rect x="0.5" y="2" width="9" height="6.5" fill="var(--navy)"/><path d="M0.5 2 L5 5.8 L9.5 2" stroke="#fff" stroke-width="0.8" fill="none"/></svg>hello@rwservices.net</li>
        <li><svg viewBox="0 0 10 10"><circle cx="5" cy="5" r="4.5" fill="var(--navy)"/><path d="M0.5 5 H9.5 M5 0.5 Q2.5 5 5 9.5 M5 0.5 Q7.5 5 5 9.5" stroke="#fff" stroke-width="0.6" fill="none"/></svg>www.rwservices.net</li>
      </ul>
    </div>
    <svg class="swoosh" width="240" height="40" viewBox="0 0 240 40" aria-hidden="true">
      <path d="M0,0 Q120,24 240,30 L240,32 Q120,28 0,3 Z" fill="var(--ochre)"/>
      <path d="M0,8 Q120,30 240,33 L240,40 L0,40 Z" fill="var(--navy)"/>
    </svg>
  </section>

  <!-- Business card, back -->
  <section class="piece card card-back card-back-a" aria-label="Business card back">
    <div class="wordmark on-dark">R&amp;W</div>
    <p class="est">Est. 1987</p>
  </section>

  <section class="piece card card-back alt card-back-b" aria-label="Business card back, alternate">
    <div class="wordmark on-dark">R&amp;W</div>
    <p class="est">Est. 1987</p>
  </section>

  <!-- Business card, landscape -->
  <section class="piece card card-wide" aria-label="Business card">
    <div class="wordmark">R&amp;W</div>
    <div class="divider"></div>
    <div class="contact">
      <p class="name">Lena Marsh</p>
      <p class="role">CEO/Founder</p>
      <p class="addr">4210 Wattle Grove Lane<br>Alice Springs, NT 0871</p>
      <ul>
        <li><svg viewBox="0 0 10 10"><path d="M2 0.5 L4 2.8 L3 4 Q4.5 6 6 7 L7.2 6 L9.5 8 L8 9.6 Q4 9 0.4 2 Z" fill="var(--navy)"/></svg>612 408 3317</li>
        <li><svg viewBox="0 0 10 10"><rect x="2.5" y="0.5" width="5" height="3" fill="var(--navy)"/><rect x="0.5" y="4" width="9" height="5.5" rx="1" fill="var(--navy)"/></svg>455 873 1206</li>
        <li><svg viewBox="0 0 10 10"><rect x="0.5" y="2" width="9" height="6.5" fill="var(--navy)"/><path d="M0.5 2 L5 5.8 L9.5 2" stroke="#fff" stroke-width="0.8" fill="none"/></svg>hello@rwservices.net</li>
        <li><svg viewBox="0 0 10 10"><circle cx="5" cy="5" r="4.5" fill="var(--navy)"/><path d="M0.5 5 H9.5 M5 0.5 Q2.5 5 5 9.5 M5 0.5 Q7.5 5 5 9.5" stroke="#fff" stroke-width="0.6" fill="none"/></svg>www.rwservices.net</li>
      </ul>
    </div>
    <svg class="swoosh" width="284" height="44" viewBox="0 0 284 44" aria-hidden="true">
      <path d="M0,0 Q140,26 284,34 L284,36 Q140,30 0,4 Z" fill="var(--ochre)"/>
      <path d="M0,8 Q140,32 284,37 L284,44 L0,44 Z" fill="var(--navy)"/>
    </svg>
  </section>

  <!-- Envelope, back -->
  <section class="piece envelope envelope-back" aria-label="Envelope back">
    <svg class="flap" width="518" height="232" viewBox="0 0 518 232" aria-hidden="true">
      <path d="M194,86 L0,230 M314,86 L518,230" stroke="#e2e2e2" stroke-width="1.2" fill="none"/>
      <path d="M0,0 H518 L508,70 Q505,86 488,86 H30 Q13,86 10,70 Z" fill="var(--ochre)"/>
    </svg>
    <div class="wordmark">R&amp;W</div>
  </section>

  <!-- Envelope, front -->
  <section class="piece envelope envelope-front" aria-label="Envelope front">
    <div class="wordmark">R&amp;W</div>
    <p class="return">62 Ridley St, PO Box<br>Barkly Creek NT. 0862</p>
    <svg class="swoosh" width="518" height="62" viewBox="0 0 518 62" aria-hidden="true">
      <path d="M0,0 Q240,42 518,48 L518,51 Q240,46 0,4 Z" fill="var(--ochre)"/>
      <path d="M0,12 Q240,50 518,52 L518,62 L0,62 Z" fill="var(--navy)"/>
    </svg>
  </section>

</main>
</body>
</html>
```